OpenHarbor Yoga Website Design

Business Logo - attached
5 pages being:
Home
About
Classes
Blog
Contact

Would like Scrolling webpage and yoga symbols to be used.

Must have's being:
Easy to navigate, Text needs to be able to be edited/updated, Enquire Now Links, More Information Links, be a secure site, SEO,

Please refer to attached document for the information for the body of the website.

Target Market(s)

Educators, Community Service, Health and Wellbeing, Mental Health

Industry/Entity Type

Yoga

Coding

Coded - Design and coding required

Number of Pages Required

5+ page

Font styles to use
Other font styles liked:
• Bella Bold BC

Colors
0094D4
00A9DD
6FCCEA
C7EBF8
E9F6FB
6B429C
8869AF
B7A5CE
E3DAEB
F3F0F8

Requirements
Must have
• Easy to navigate, Text needs to be able to be edited/updated, Enquire Now Links, More Information Links, be a secure site, SEO,
Nice to have
• Scrolling webpage, yoga symbols

```html
<!DOCTYPE html>
<html lang="en">
<head>
<meta charset="utf-8">
<title>OpenHarbor Yoga</title>
<link href="https://fonts.googleapis.com/css2?family=Poppins:wght@400;500;600;700;800&family=Yellowtail&display=swap" rel="stylesheet">
<style>
:root{
  --purple:#6b429c;
  --purple-mid:#8869af;
  --purple-soft:#b7a5ce;
  --purple-pale:#e3daeb;
  --purple-light:#c8b4e6;
  --ink:#1b1b1b;
  --white:#ffffff;
  --dark:#1c1719;
  --footer:#3a3638;
}
*{margin:0;padding:0;box-sizing:border-box}
html,body{width:1200px;height:2431px;overflow:hidden}
body{position:relative;font-family:'Poppins',sans-serif;background:var(--white);color:var(--ink)}
.abs{position:absolute}
.script{font-family:'Yellowtail',cursive;font-weight:400}

.hero-bg{left:0;top:0;width:1200px;height:700px}
.nav{left:111px;top:59px;width:977px;height:66px;background:var(--white);border-radius:33px}
.brand{left:44px;top:17px;display:flex;align-items:center;gap:10px;font-weight:700;font-size:17px;color:var(--purple)}
.brand-dot{width:28px;height:28px;border-radius:50%;background:var(--ink)}
.nav-links{left:351px;top:22px;display:flex;gap:33px;font-weight:600;font-size:16px;color:#2a2a2a}
.nav-links .active{color:var(--purple)}
.btn-start{left:828px;top:18px;width:116px;height:31px;border-radius:16px;background:var(--purple);color:var(--white);font-weight:700;font-size:13px;display:flex;align-items:center;justify-content:center}

.hero-title{left:128px;top:272px;font-size:56px;color:var(--white);white-space:nowrap}
.hero-text{left:111px;top:363px;width:489px;font-size:15px;line-height:18.6px;color:var(--white);text-align:justify}
.btn-learn{left:290px;top:489px;width:132px;height:37px;border-radius:12px;background:var(--ink);color:var(--white);font-weight:700;font-size:13px;display:flex;align-items:center;justify-content:center}
.hero-photo{left:774px;top:351px;width:300px;height:300px;border-radius:50%;background:radial-gradient(circle at 50% 38%,#f7e2b8 0%,#d9c2b0 40%,#7d6d6b 75%,#2d2a2d 100%);box-shadow:0 14px 18px rgba(0,0,0,.25)}

.benefits-title{left:0;top:690px;width:1200px;text-align:center;font-size:52px;color:var(--ink)}
.benefits-text{left:260px;top:780px;width:680px;text-align:center;font-size:17.5px;line-height:25px;color:#333}

.card{top:943px;width:280px;height:400px;background:var(--purple-soft);border:3px solid #7a4fae}
.card-icon{top:-62px;left:78px;width:120px;height:120px;border-radius:50%;background:#7a4fae;display:flex;align-items:center;justify-content:center}
.card-icon span{width:46px;height:46px;border-radius:50%;background:var(--white);opacity:.95}
.card h3{position:absolute;top:66px;left:0;width:100%;text-align:center;font-size:34px;color:var(--ink)}
.card h3 em{font-style:normal;color:#7a4fae}
.card ul{position:absolute;top:107px;left:5px;right:6px;list-style:none;font-size:13.3px;font-weight:500;line-height:24.5px;color:#1d1d1d}
.card li{padding-left:9px;text-indent:-9px}
.card li::before{content:"• "}

.about{left:0;top:1429px;width:1200px;height:594px;background:linear-gradient(180deg,#3b3034 0%,#2a2326 45%,#151112 100%)}
.about-title{left:0;top:1510px;width:1170px;text-align:right;padding-right:517px;font-size:54px;color:var(--white)}
.about-text{left:128px;top:1593px;width:515px;font-size:17.3px;line-height:24px;color:var(--white)}
.about-text p{margin-bottom:24px;text-align:justify}
.about-links{left:211px;top:1900px;display:flex;gap:108px;font-weight:700;font-size:18px}
.about-links a{color:var(--purple-light);text-decoration:none;border-bottom:2px solid var(--purple-light);padding-bottom:1px}
.about-panel{left:773px;top:1595px;width:298px;height:278px;background:#7a4fae}
.panel-name{left:183px;top:92px;width:100px;text-align:center;font-size:15px;font-weight:500;color:var(--purple-pale);line-height:20px}
.panel-social{left:200px;top:213px;display:flex;gap:26px}
.panel-social span{width:25px;height:25px;border-radius:50%;border:3px solid var(--purple-pale)}
.about-photo{left:685px;top:1631px;width:238px;height:207px;background:linear-gradient(135deg,#cfd7de 0%,#b6c4ce 55%,#7fb2d3 100%)}

.footer{left:0;top:2022px;width:1200px;height:409px;background:var(--footer)}
.foot-brand{left:0;top:2075px;width:1200px;text-align:center;font-size:20px;font-weight:600;color:var(--purple-light)}
.foot-nav{left:0;top:2165px;width:1200px;display:flex;justify-content:center;gap:35px;font-weight:700;font-size:17.5px;color:var(--purple-light)}
.foot-info{left:0;top:2209px;width:1200px;text-align:center;font-size:17px;line-height:30px;color:var(--white)}
.foot-social{left:563px;top:2307px;display:flex;gap:27px}
.foot-social span{width:24px;height:24px;border-radius:50%;border:3px solid var(--purple-light)}
.foot-rule{left:110px;top:2372px;width:977px;height:1px;background:#8c8c8c}
.copyright{left:0;top:2390px;width:1200px;text-align:center;font-size:16px;color:var(--white)}
</style>
</head>
<body>

<svg class="abs hero-bg" viewBox="0 0 1200 700" aria-hidden="true">
  <defs>
    <linearGradient id="heroGrad" x1="0" y1="0" x2="1" y2="0.3">
      <stop offset="0" stop-color="#6e43a0"/>
      <stop offset="0.55" stop-color="#8e70b4"/>
      <stop offset="1" stop-color="#b39fcf"/>
    </linearGradient>
  </defs>
  <polygon points="0,0 1200,0 1200,407 394,664 0,690" fill="url(#heroGrad)"/>
</svg>

<header class="abs nav">
  <div class="abs brand"><span class="brand-dot"></span>OpenHarbor Yoga</div>
  <nav class="abs nav-links">
    <span class="active">Home</span><span>About</span><span>Classes</span><span>Blog</span><span>Contact</span>
  </nav>
  <div class="abs btn-start">Get Started</div>
</header>

<h1 class="abs hero-title script">Welcome to OpenHarbor Yoga...</h1>
<p class="abs hero-text">OpenHarbor Yoga believe that you are never too young to benefit from and fall in love with yoga. My aim is to EMPOWER kids and teens to thrive by teaching life skills in Yoga, Mindfulness and Breathing techniques to deal with daily challenges and big emotions.</p>
<div class="abs btn-learn">Learn More</div>
<div class="abs hero-photo" role="img" aria-label="Photo of a person meditating with arms raised at sunset by the water"></div>

<h2 class="abs benefits-title script">Benefits</h2>
<p class="abs benefits-text">The benefits of yoga can last a lifetime. It is my aim &amp; passion to introduce yoga to kids of all ages and backgrounds so that they can not only experience the benefits of yoga but fall in love with the practice.</p>

<section class="abs card" style="left:111px">
  <div class="abs card-icon" role="img" aria-label="Meditation icon"><span></span></div>
  <h3 class="script">Healthy <em>Bodies</em></h3>
  <ul>
    <li>Develops strong, flexible and healthy bodies</li>
    <li>Promotes spinal alignment and good posture</li>
    <li>Builds energy and stamina</li>
    <li>Improves internal physical function - organs, digestion, elimination, circulation, and blood flow.</li>
    <li>Helps breathing and lung capacity</li>
    <li>Teaches the enjoyment of movement</li>
    <li>Works the ‘whole’ body</li>
  </ul>
</section>
<section class="abs card" style="left:459px">
  <div class="abs card-icon" role="img" aria-label="Mind icon"><span></span></div>
  <h3 class="script">Healthy <em>minds</em></h3>
  <ul>
    <li>Cultivates confidence and self-esteem</li>
    <li>Develops concentration and attention</li>
    <li>Clears the mind for better clarity and decision making</li>
    <li>Helps relax and sleep better</li>
    <li>Calms the nervous system</li>
    <li>Learns to cope with stressful situations</li>
    <li>Balances emotions</li>
  </ul>
</section>
<section class="abs card" style="left:807px">
  <div class="abs card-icon" role="img" aria-label="Spirit icon"><span></span></div>
  <h3 class="script">Healthy <em>Spirits</em></h3>
  <ul>
    <li>Fosters creativity, expression and imagination</li>
    <li>Cultivates kindness to themselves and others</li>
    <li>Cultivates respect for self and others</li>
    <li>Builds balance and inner quiet</li>
    <li>Builds inner strength and resilience</li>
    <li>Teaches self-awareness</li>
    <li>Focuses on positive self-talk</li>
  </ul>
</section>

<section class="abs about" role="img" aria-label="Dusk landscape background with a silhouette doing yoga"></section>
<h2 class="abs about-title script">About Us</h2>
<div class="abs about-text">
  <p>My name is Renata, and I am the creator &amp; facilitator of OpenHarbor Yoga.</p>
  <p>With the increasing numbers of youth mental health, I have started OpenHarbor Yoga wanting to assist children and teens with their mental health for life, with the magic of yoga.</p>
  <p>I had always wanted to teach children, but had never found the right platform to do so… That was until I found yoga!</p>
  <p>I genuinely believe the practice of yoga and mindfulness</p>
</div>
<div class="abs about-links"><a href="#">Enquire Now</a><a href="#">More Information</a></div>
<div class="abs about-panel">
  <div class="abs panel-name">OpenHarbor Yoga</div>
  <div class="abs panel-social"><span></span><span></span></div>
</div>
<div class="abs about-photo" role="img" aria-label="Photo of a woman in a seated yoga twist on a mat"></div>

<footer class="abs footer"></footer>
<div class="abs foot-brand">OpenHarbor Yoga</div>
<nav class="abs foot-nav"><span>Home</span><span>About</span><span>Classes</span><span>Blog</span><span>Contact</span></nav>
<div class="abs foot-info">
  Address: Fernvale, Victoria Australia 3790<br>
  ABN:&nbsp; 12 345 678 901 | Website: openharboryoga.com.au<br>
  Phone: 0400 123 456 | Mail: hello@openharboryoga.com
</div>
<div class="abs foot-social"><span></span><span></span></div>
<div class="abs foot-rule"></div>
<div class="abs copyright">Copyrights 2023 OpenHarbor Yoga. All Rights Reserved.</div>

</body>
</html>
```